Web Design Project

Desisgn a new style for the proposed website as per the attached link. The logo will remain as is, and it is likely that the colours will be as per the attached style guide.

Otherwise look and feel, icons, layout, images are within scope.

Current prosposed home page:
http://vantrelux-newsite.pagemorrowhost.com/index

Target Market(s)

Typically, large organisations from any industry such as Airlines, banks, Govt agencies.

Could be operational executives, business improvement specialists, bsuienss analysts.

```html
<!DOCTYPE html>
<html lang="en">
<head>
<meta charset="utf-8">
<title>Vantrelux – Business Transformations</title>
<link href="https://fonts.googleapis.com/css2?family=Open+Sans:wght@400;600;700&display=swap" rel="stylesheet">
<style>
  :root {
    --navy: #2c4679;
    --navy-dark: #243d6c;
    --blue: #4a7bb8;
    --blue-tab: #3d6fb3;
    --rule: #a9bfdc;
    --text: #3a3a3a;
    --heading: #2c4679;
    --yellow: #f2c200;
    --white: #ffffff;
    --tile-border: #c9c9c9;
    --footer-link: #e6eef8;
    --footer-head: #233b66;
  }
  * { margin: 0; padding: 0; box-sizing: border-box; }
  html, body { width: 907px; height: 1200px; overflow: hidden; background: var(--white); }
  body { position: relative; font-family: "Open Sans", sans-serif; color: var(--text); }

  .masthead { position: absolute; left: 17px; top: 0; width: 876px; height: 87px; background: var(--navy); }
  .brand { position: absolute; left: 30px; top: 28px; display: flex; align-items: center; gap: 8px; color: var(--white); font-size: 22px; font-weight: 400; letter-spacing: .3px; }
  .brand-dot { width: 32px; height: 32px; border-radius: 50%; background: #5a8fd0; }

  .main-nav { position: absolute; left: 17px; top: 87px; width: 876px; height: 37px; border-bottom: 1px solid var(--rule); display: flex; font-size: 13px; letter-spacing: .4px; }
  .main-nav a { color: #444; text-decoration: none; display: block; line-height: 37px; padding: 0 18px; }
  .main-nav a.active { background: var(--blue-tab); color: var(--white); padding: 0 22px; }
  .main-nav a + a { margin-left: 2px; }

  .hero { position: absolute; left: 17px; top: 137px; width: 876px; height: 267px; background: linear-gradient(90deg, #4b3a2c 0%, #6a5442 25%, #2d2b40 45%, #4a2a3a 62%, #2f4a2a 80%, #7a6a1f 100%); }
  .hero-title { position: absolute; left: 401px; top: 127px; color: var(--white); font-size: 29px; font-weight: 700; letter-spacing: .6px; }
  .hero-sub { position: absolute; left: 401px; top: 168px; color: var(--yellow); font-size: 27px; line-height: 31px; font-weight: 400; }

  .services { position: absolute; left: 17px; top: 419px; width: 876px; height: 140px; }
  .service { position: absolute; top: 0; width: 126px; height: 140px; border-bottom: 1px solid var(--rule); text-align: center; }
  .service-art { width: 126px; height: 97px; border: 1px solid var(--tile-border); display: flex; align-items: center; justify-content: center; }
  .service-art span { display: block; width: 62px; height: 62px; border-radius: 8px; }
  .service-label { margin-top: 5px; font-size: 12.5px; line-height: 15px; letter-spacing: .5px; color: #444; }

  .intro { position: absolute; left: 17px; top: 580px; width: 530px; }
  .intro h1 { font-size: 21px; font-weight: 400; color: var(--heading); margin-bottom: 10px; letter-spacing: .2px; }
  .intro p { font-size: 12px; line-height: 16.5px; margin-bottom: 6px; letter-spacing: .15px; }
  .intro ul { list-style: none; margin-top: 6px; }
  .intro li { font-size: 11.5px; line-height: 14px; margin-bottom: 8.6px; padding-left: 20px; position: relative; }
  .intro li::before { content: ""; position: absolute; left: 6px; top: 5px; width: 5px; height: 5px; border-radius: 50%; background: var(--navy); }

  .video { position: absolute; left: 581px; top: 582px; width: 312px; height: 232px; background: #000; }
  .video-play { position: absolute; left: 130px; top: 90px; width: 52px; height: 32px; border-radius: 5px; background: linear-gradient(#9a9a9a, #5e5e5e); }
  .video-bar { position: absolute; left: 0; bottom: 0; width: 312px; height: 16px; background: linear-gradient(#eeeeee, #c8c8c8); font-size: 8px; color: #222; }
  .video-bar .track { position: absolute; left: 26px; top: 6px; width: 186px; height: 4px; background: #888; border-radius: 2px; }
  .video-bar .time { position: absolute; left: 224px; top: 3px; }

  .news { position: absolute; left: 581px; top: 832px; width: 312px; height: 175px; background: var(--navy); color: var(--white); }
  .news h2 { font-size: 16px; font-weight: 400; padding: 7px 14px 0; height: 29px; border-bottom: 1px solid #5877ab; }
  .news-item { padding: 3px 14px 8px; border-bottom: 1px solid #5877ab; }
  .news-date { display: inline-block; background: var(--blue-tab); color: #cfe0f5; font-size: 11px; padding: 0 5px; line-height: 16px; margin-bottom: 4px; }
  .news-item p { font-size: 11.5px; line-height: 15.5px; }
  .news-more { position: absolute; right: 12px; bottom: 4px; background: var(--blue-tab); color: #cfe0f5; font-size: 10px; line-height: 16px; padding: 0 8px; text-decoration: none; }

  .site-footer { position: absolute; left: 17px; top: 1025px; width: 876px; height: 175px; background: var(--blue); }
  .footer-col { position: absolute; top: 16px; }
  .footer-col h3 { font-size: 11.5px; font-weight: 600; color: var(--footer-head); margin-bottom: 6px; letter-spacing: .3px; }
  .footer-col a { display: block; font-size: 11.5px; line-height: 19.5px; color: var(--footer-link); text-decoration: none; }
  .copyright { position: absolute; left: 0; bottom: 0; width: 876px; height: 19px; border-top: 1px solid #3a649c; text-align: center; font-size: 9.5px; line-height: 18px; color: #27406f; }
</style>
</head>
<body>

<header class="masthead">
  <div class="brand"><span class="brand-dot"></span>vantrelux</div>
</header>

<nav class="main-nav">
  <a class="active" href="#">HOME</a>
  <a href="#">PRODUCTS</a>
  <a href="#">SERVICES</a>
  <a href="#">SOLUTIONS</a>
  <a href="#">RESOURCES</a>
  <a href="#">CUSTOMER STORIES</a>
  <a href="#">ABOUT US</a>
  <a href="#">CONTACT</a>
</nav>

<section class="hero" role="img" aria-label="Close-up photograph of colourful abacus beads on wooden rods">
  <div class="hero-title">Business Transformations</div>
  <div class="hero-sub">Reduce Risk and cost<br>Increase benefits</div>
</section>

<section class="services">
  <div class="service" style="left:0">
    <div class="service-art"><span role="img" aria-label="Icon of people with light bulbs" style="background:#1f4e86"></span></div>
    <div class="service-label">Knowledge<br>Management</div>
  </div>
  <div class="service" style="left:149px">
    <div class="service-art"><span role="img" aria-label="Icon of circular arrows with blue blocks" style="background:linear-gradient(135deg,#c8ccd2,#2d6fc2)"></span></div>
    <div class="service-label">Continuous<br>Improvement</div>
  </div>
  <div class="service" style="left:300px">
    <div class="service-art"><span role="img" aria-label="Illustration of a rising colourful trend line" style="background:linear-gradient(45deg,#e08a3a,#e6d14a,#7bb04a);height:14px"></span></div>
    <div class="service-label">Business<br>Transformation</div>
  </div>
  <div class="service" style="left:450px">
    <div class="service-art"><span role="img" aria-label="Icon of a computer monitor" style="background:linear-gradient(135deg,#3a8de0,#a9acb3)"></span></div>
    <div class="service-label">System<br>Requirements</div>
  </div>
  <div class="service" style="left:601px">
    <div class="service-art"><span role="img" aria-label="Icon of a green process modelling board" style="background:linear-gradient(135deg,#3fa35a,#1c5e2c)"></span></div>
    <div class="service-label">Business<br>Process Modeling</div>
  </div>
  <div class="service" style="left:750px">
    <div class="service-art"><span role="img" aria-label="Icon of a classical columned building" style="background:linear-gradient(#6c78d6,#3a44a8)"></span></div>
    <div class="service-label">Governance<br>&amp; Compliance</div>
  </div>
</section>

<article class="intro">
  <h1>We power and de-risk business transformations</h1>
  <p>Operational excellence and business transformation is achieved by understanding and capturing every detail of your business. High performing companies have a single view of the complex relationships between systems, processes and people supported by in depth organizational knowledge. Vantrelux’s Operational Business Management System (OBMS) empowers and de-risks large transformation initiatives enabling continuous improvement for high performing organizations.</p>
  <p>An OBMS captures the DNA of your business. It links people, processes and systems in a way that visualizes how your organization works today, and how it may change in the future. This information is managed in a re-usable and extendable framework and is distributed to the many stakeholders in a form that meets their individual needs.</p>
  <p>This unique way of reaching, engaging and empowering everyone involved in your business allows you to continually excel in your operations and reduce costs while maintaining compliance and governance standards. Vantrelux’s OBMS allows you to:</p>
  <ul>
    <li>Build a knowledge management system that captures and reuses your expertise.</li>
    <li>Undertake business transformations that reduce risk and cost and increase the benefits.</li>
    <li>Implement continuous improvement as a natural part of your business processes.</li>
    <li>Create business process models that are understood to business users.</li>
    <li>Create systems requirements that relate business processes to IT systems capability.</li>
    <li>Deliver governance and compliance through auditable and traceable operational systems.</li>
  </ul>
</article>

<section class="video" aria-label="Video player">
  <div class="video-play"><svg width="52" height="32" viewBox="0 0 52 32"><polygon points="21,9 21,23 32,16" fill="#222"/></svg></div>
  <div class="video-bar">
    <svg width="20" height="16" viewBox="0 0 20 16" style="position:absolute;left:4px;top:0"><polygon points="5,4 5,12 12,8" fill="#222"/></svg>
    <div class="track"></div>
    <span class="time">0:00 / 0:00</span>
  </div>
</section>

<aside class="news">
  <h2>News &amp; Events</h2>
  <div class="news-item">
    <span class="news-date">10 - 11 - 2012</span>
    <p>Lorem Ipsum is simply dummy text of the printing and typesetting industry.</p>
  </div>
  <div class="news-item">
    <span class="news-date">10 - 11 - 2012</span>
    <p>Lorem Ipsum is simply dummy text of the printing and typesetting industry.</p>
  </div>
  <a class="news-more" href="#">Read more</a>
</aside>

<footer class="site-footer">
  <div class="footer-col" style="left:32px">
    <h3>PRODUCTS</h3>
    <a href="#">Mapwise</a>
    <a href="#">Vantrelux Modeler</a>
    <a href="#">- System Requirements Modeler</a>
    <a href="#">- Performance Improvement Modeler</a>
    <a href="#">- Enterprise Architect Modeler</a>
    <a href="#">- Corporate Governance Modeler</a>
  </div>
  <div class="footer-col" style="left:312px">
    <h3>SERVICES</h3>
    <a href="#">Coaching &amp; Mentoring</a>
    <a href="#">Technical Services</a>
  </div>
  <div class="footer-col" style="left:520px">
    <h3>NEWS &amp; EVENTS</h3>
    <a href="#">Announcements</a>
    <a href="#">Technical Notes</a>
  </div>
  <div class="footer-col" style="left:694px">
    <h3>TRAINING &amp; SUPPORT</h3>
    <a href="#">Text-Based Tutorials</a>
    <a href="#">Tutorial Movies</a>
    <a href="#">Knowledge Base</a>
    <a href="#">Forums</a>
    <a href="#">Training Courses</a>
  </div>
  <div class="copyright">© Copyright VANTRELUX 2012 - All Rights Reserved TERMS &amp; CONDITIONS | PRIVACY POLICY | MAINTENANCE POLICY</div>
</footer>

</body>
</html>
```